Either a trifold or double sided flyer/brochure

A flyer to help spark interest in a historic preservation project in Peterborough, NH--looking for something that captures the early 19th century rural village and mill times--American Primitive, Shaker, Cross Stitch Sampler...must be able to highlight home history as well as have all owners of house on a single page. Word document attached--can also provide files for the house painting, color photos, borrell photo, advertising photo or part of original settler map.
I like this brochure
http://tessavornick.com/wordpress/dell-lodge-museum-brochure/
community stakeholders, residents,
Historic Preservation, House Museums.

```html
<!DOCTYPE html>
<html lang="en">
<head>
<meta charset="utf-8">
<title>The Hartwell Homestead – Trifold Brochure</title>
<link rel="stylesheet" href="https://fonts.googleapis.com/css2?family=Noto+Serif:ital,wght@0,400;0,700;1,400&family=Open+Sans:wght@400;600&family=Figtree:wght@500;700&family=Anton&display=swap">
<style>
:root{
  --charcoal:#33292d;
  --parchment:#e6dfd1;
  --red:#b2211b;
  --tan:#dccaa5;
  --ink:#2a2424;
  --page:#f2f1ef;
  --rule:#4a3f43;
}
*{box-sizing:border-box;margin:0;padding:0}
html,body{width:1200px;height:2549px;overflow:hidden;background:var(--page)}
.canvas{position:relative;width:1200px;height:2549px}
.spread{position:absolute;left:42px;width:1116px;height:789px;display:flex;box-shadow:0 4px 14px rgba(0,0,0,.25)}
.spread--outside{top:470px}
.spread--inside{top:1296px}
.panel{position:relative;width:372px;height:100%;overflow:hidden}
.panel--dark{background:var(--charcoal)}
.panel--parchment{background:var(--parchment)}
.ph{position:absolute}

/* owners panel */
.owners__band{position:absolute;left:0;right:0;top:65px;height:112px;background:var(--red)}
.owners__painting{position:absolute;left:35px;top:37px;width:302px;height:166px;border:5px solid #fff;background:linear-gradient(180deg,#6f7f93 0%,#3c4d6b 45%,#4f5b3a 75%,#37402a 100%);box-shadow:0 3px 8px rgba(0,0,0,.5)}
.owners__title{position:absolute;left:0;right:0;top:221px;text-align:center;font:400 18.5px/1.18 "Noto Serif",serif;color:var(--tan)}
.owners__list{position:absolute;left:18px;right:20px;top:284px;list-style:none}
.owners__row{display:flex;align-items:center;justify-content:space-between;height:46px;border-bottom:1px solid var(--rule);font:400 9.4px/1.35 "Open Sans",sans-serif;color:#f1ece6}
.owners__row:last-child{border-bottom:none}
.owners__years{flex:0 0 74px;height:20px;background:var(--red);color:#fff;font:500 10.5px/20px "Figtree",sans-serif;text-align:center;clip-path:polygon(7px 0,100% 0,100% 100%,0 100%)}

/* community panel */
.invite{position:absolute;left:38px;top:60px;width:298px;height:190px;border:1px dashed #a89f8f;text-align:center;padding-top:40px}
.invite__mark{position:absolute;left:50%;top:-13px;width:36px;height:36px;margin-left:-18px;background:var(--red);border-radius:3px}
.invite__title{font:700 21.5px/1.2 "Noto Serif",serif;color:var(--ink)}
.invite__text{margin-top:8px;font:400 16px/1.25 "Noto Serif",serif;color:var(--ink)}
.map{left:35px;top:270px;width:302px;height:284px;border:5px solid #fff;background:linear-gradient(135deg,#f4f3ee,#dcdad2);box-shadow:0 2px 6px rgba(0,0,0,.25)}
.ad{position:absolute;left:0;right:0;top:587px;text-align:center;color:var(--ink);font:400 15.5px/1.22 "Noto Serif",serif}
.ad__name{font-weight:700;font-size:23px;line-height:1.1}
.ad__trade{font-style:italic}
.ad__street{font-weight:700;font-size:17px}

/* cover */
.cover__photo{inset:0;background:radial-gradient(ellipse at 60% 40%,#8a7454 0%,#5a4a35 45%,#2d241a 100%)}
.cover__ghost{position:absolute;left:18px;top:20px;writing-mode:vertical-rl;transform:rotate(180deg);font:400 120px/1 "Anton",sans-serif;color:rgba(230,215,185,.22);letter-spacing:2px}
.cover__band{position:absolute;left:0;right:0;top:604px;height:113px;background:var(--red);padding:6px 0 0 52px}
.cover__title{font:700 34.5px/1.2 "Figtree",sans-serif;color:#fff}
.cover__title span{display:inline-block;border-bottom:3px solid #fff;line-height:1.05}
.cover__sub{position:absolute;left:52px;top:732px;font:500 13.5px/1.35 "Figtree",sans-serif;color:var(--tan);letter-spacing:.4px}

/* photo wall */
.photo-autumn{left:0;top:0;width:372px;height:264px;background:linear-gradient(180deg,#c9772a 0%,#8e6a2a 35%,#c9a84f 60%,#6e4a24 100%)}
.photo-couple{left:0;top:268px;width:372px;height:227px;background:linear-gradient(180deg,#8b8178,#4d4640 60%,#2f2a26)}
.photo-stair{left:0;top:499px;width:224px;height:290px;background:linear-gradient(160deg,#d8d0c4,#8a5a3a 55%,#4a2d1c)}
.photo-latch{left:229px;top:499px;width:143px;height:165px;background:linear-gradient(135deg,#5f8e8a,#3d5554 60%,#6a3d2c)}
.photo-snow{left:229px;top:669px;width:143px;height:120px;background:linear-gradient(180deg,#c9ccd0,#a89452 55%,#eceeef)}
.caption{position:absolute;left:0;height:18px;padding:0 20px 0 19px;background:var(--red);color:var(--tan);font:700 11.5px/18px "Noto Serif",serif;clip-path:polygon(0 0,100% 0,calc(100% - 10px) 100%,0 100%)}
.caption--mill{top:248px}
.caption--couple{top:478px}

/* history panel */
.history{position:absolute;left:38px;top:20px;width:298px;height:722px;border:1px dashed #a89f8f;padding:18px 12px 0;color:var(--ink);box-shadow:0 8px 8px -6px rgba(0,0,0,.25)}
.history__title{text-align:center;font:700 19.5px/1.2 "Noto Serif",serif}
.history__place{display:block;font-weight:400;font-style:italic}
.history__body p{margin-top:10px;font:400 7.7px/1.45 "Open Sans",sans-serif;text-align:justify;text-align-last:center}
.history__body p:first-child{margin-top:9px}

/* back cover */
.back{background:#fff}
.back__photo{left:0;top:0;width:372px;height:600px;background:linear-gradient(180deg,#9a9a9a 0%,#6e6e6e 40%,#bdbdbd 80%,#fff 100%)}
.back__title{position:absolute;left:0;right:0;top:604px;text-align:center;font:400 70px/.98 "Anton",sans-serif;text-transform:uppercase}
.back__title .line1{color:#1b1717;font-size:64px}
.back__title .line2{color:var(--red);display:block;font-size:76px}
</style>
</head>
<body>
<main class="canvas">

  <section class="spread spread--outside" aria-label="Brochure outside spread">
    <div class="panel panel--dark owners">
      <div class="owners__band"></div>
      <div class="owners__painting" role="img" aria-label="Folk painting of the white farmhouse and barn"></div>
      <h2 class="owners__title">Owners of 47 Orchard Street<br>Alder Falls, Vermont</h2>
      <ul class="owners__list">
        <li class="owners__row"><span>Ezra Greene (grandson of Caleb Greene) owned the land</span><span class="owners__years">1829</span></li>
        <li class="owners__row"><span>Nathan P. Hartwell and Lydia (Prentice) Hartwell</span><span class="owners__years">1829-1831</span></li>
        <li class="owners__row"><span>Deacon Josiah Ellery and Abigail(Marsh) Ellery(Baptist)</span><span class="owners__years">1831-1842</span></li>
        <li class="owners__row"><span>Amos Reed Ashby and Hannah (Tolland) Ashby<br>(mortgage between Oliver Marsh and Ashby is 1848)</span><span class="owners__years">1842-1880</span></li>
        <li class="owners__row"><span>Clara Beth Ashby</span><span class="owners__years">1880-1901</span></li>
        <li class="owners__row"><span>Silas Carrow</span><span class="owners__years">1901-1907</span></li>
        <li class="owners__row"><span>Arthur Lane Borrell and Edith M. (Dunmore) Borrell</span><span class="owners__years">1907-1959</span></li>
        <li class="owners__row"><span>Ruth (Borrell) Lindquist and Carl E. Lindquist<br>(Ruth was born in house on March 12, 1914)</span><span class="owners__years">1958-2001</span></li>
        <li class="owners__row"><span>Daniel K. Oberlander and Sofia Reyes Oberlander<br>(Daniel was nephew of Ruth (Borrell) Lindquist)</span><span class="owners__years">2001-2018</span></li>
        <li class="owners__row"><span>Brookhaven</span><span class="owners__years">2018-2023</span></li>
        <li class="owners__row"><span>Thomas R. Carvalho and Peter J. Pennington, Jr.</span><span class="owners__years">2023</span></li>
      </ul>
    </div>

    <div class="panel panel--parchment community">
      <div class="invite">
        <span class="invite__mark" aria-hidden="true"></span>
        <h3 class="invite__title">They invite<br>you to join their<br>Townhall Circle Group</h3>
        <p class="invite__text">Hartwell Homestead c. 1829,<br>Borrells Corner, Alder Falls,<br>Vermont</p>
      </div>
      <div class="ph map" role="img" aria-label="Section of the early settler lot map around the mill farm"></div>
      <div class="ad">
        <p class="ad__name">W.J. ASHBY</p>
        <p class="ad__trade">Wool Carder, Cloth Dresser</p>
        <p>and Wool Dryer</p>
        <p>Garments of all kinds re-dyed,</p>
        <p>Dress prepared for family use,</p>
        <p>with directions for coloring.</p>
        <p class="ad__street">ORCHARD STREET.</p>
        <p>Alder Falls, Vt., June 3 1881</p>
      </div>
    </div>

    <div class="panel cover">
      <div class="ph cover__photo" role="img" aria-label="Sepia portrait of a woman in a dark dress with a lace collar"></div>
      <div class="cover__ghost" aria-hidden="true">HARTWELL</div>
      <div class="cover__band">
        <h1 class="cover__title"><span>THE HARTWELL</span><br><span>HOMESTEAD</span></h1>
      </div>
      <p class="cover__sub">HISTORY C. 1829<br>ALDER FALLS, VERMONT</p>
    </div>
  </section>

  <section class="spread spread--inside" aria-label="Brochure inside spread">
    <div class="panel panel--parchment gallery">
      <div class="ph photo-autumn" role="img" aria-label="Yellow farmhouse and barn among autumn trees"></div>
      <span class="caption caption--mill">Advertising for the Ashby Mill</span>
      <div class="ph photo-couple" role="img" aria-label="Old photograph of an elderly couple seated indoors"></div>
      <span class="caption caption--couple">Arthur and Edith Borrell</span>
      <div class="ph photo-stair" role="img" aria-label="Narrow wooden staircase inside the house"></div>
      <div class="ph photo-latch" role="img" aria-label="Hand-forged iron door latch on a painted door"></div>
      <div class="ph photo-snow" role="img" aria-label="The homestead in winter snow"></div>
    </div>

    <div class="panel panel--parchment">
      <article class="history">
        <h2 class="history__title">The Hartwell<br>Homestead History c. 1829<span class="history__place">Alder Falls, Vermont</span></h2>
        <div class="history__body">
          <p>In 1829, Nathan P. Hartwell and his wife, Lydia (Prentice) Hartwell purchased 30 acres from Ezra Greene on the Ashwater River, north of Pellam's Woolen Mill in Lower Alder Falls. This parcel was carved out of lot #19 which was comprised of 240 acres that were deeded to Caleb Greene (Ezra Greene's grandfather) by Jeremiah Fenwick and John Hale on May 9, 1765. It is believed that Hartwell, who was a blacksmith, built the house that currently stands at 47 Orchard Street in Alder Falls. He also built his forge on the site down by the river. It is likely that much of the forged hardware in the home was crafted by him. Feeling the need to leave Alder Falls for a new frontier, Hartwell left town with his brother, Bramwell, to purchase land in the emerging communities on the western frontier of New York. Before doing so, Hartwell sold the home, shop and buildings to Josiah Ellery and his wife Abigail (Marsh) Ellery in 1831.</p>
          <p>By trade, Josiah Ellery was a cloth dresser and wool-carder. He was also a deeply religious man and served as deacon in the emerging, but still quite small, Baptist community. In those days, small groups of the Baptists and Methodists met in the Alden Home for bible study, prayers and singing. The Aldens were well known abolitionists and their house served as a stop on the Underground Railroad. Deacon Ellery died in 1842 and his estate was managed by Oliver Marsh—very likely a relative of Abigail—who protected Abigail's dower. The property was then sold to Amos Reed Ashby and his wife Hannah (Tolland) Ashby.</p>
          <p>Amos was quite industrious and continued to expand the wool mill. He was an early investor in the Hillcrest Railroad and ceded a right of way to the railroad on the homestead. The mill eventually came under the control of his son, Walter J. Ashby, and operated until it burned down on October 8, 1877. Amos passed away in 1880 and left the home to Clara Beth Ashby who was most commonly known as "Beth."</p>
          <p>Beth Ashby was approached in 1894 by Hattie Pellam, the owner of the Pellam's Mill Complex, to ask if she would be willing to rent out the home to a couple from the city. This turned out to be Louisa and Henry Larkin, the founders of the Larkin Colony, who ended up spending their first summer in Alder Falls in the home. Louisa recalls in her writings: "You can't fail to remember the two-story farmhouse almost across the road from the iron bridge, now occupied by the Borrell Family. It had never been painted and was a lovely soft gray in color. There were really only four rooms and a kitchen, spotlessly clean and adequately furnished, which really didn't mean much but some chairs, tables and beds. Then in the kitchen was something that fascinated me, a stone bowl into which the clearest of water was all the time pouring and then running off into a drain...."</p>
          <p>The Borrells lived in this home for the longest time of any owner—and some refer to this area before the bridge, as Borrells Corner. This moment of stewardship began under Arthur Lane Borrell and his wife Edith M. (Dunmore) Borrell around 1907 and lasted until 2018 when a descendant sold the home. The house is now under the stewardship of Thomas R. Carvalho and Peter J. Pennington, Jr. and will be undergoing a significant restoration.</p>
        </div>
      </article>
    </div>

    <div class="panel back">
      <div class="ph back__photo" role="img" aria-label="Black and white photo of the clapboard house gable with tree shadows"></div>
      <h2 class="back__title"><span class="line1">THE HARTWELL</span><span class="line2">HOMESTEAD</span></h2>
    </div>
  </section>

</main>
</body>
</html>
```